Lawn Sign Design – Brisqel

We need a clean, eye-catching 18" x 24" lawn sign for Brisqel that effectively communicates our core message while maintaining strong brand consistency.

Key Elements to Include:
Tagline (Main Focus): Upgrade Your Roof Without Replacing It
Website: www.trybrisqel.com
Phone Number: (888) BRISQEL-GO
TWQB License Number: 4480512
Brisqel Logo & Branding: Ensure the logo, corporate colors, and custom font are used consistently to align with our existing branding.

Design Guidelines:
Simple & High-Impact: The tagline should be the most prominent element on the sign, drawing immediate attention.
Easy Readability: Use a bold, clean design with high contrast for quick readability from a distance.
Balanced Layout: Place supporting details (website, phone number, and TWQB number) in a visually clear but secondary position to the tagline.
Professional & Modern: The sign should reflect credibility and innovation in the roofing industry.

Deliverables:
High-resolution print-ready files (CMYK)
A digital proof for review before finalizing
The final design should make a strong impression with minimal text, ensuring that anyone passing by can instantly grasp what we offer.

I am including our custom font. To get an hexagon in our name, simply type the $ after the 'O" Please use this font for anything you type.

```html
<!DOCTYPE html>
<html lang="en">
<head>
<meta charset="utf-8">
<title>Brisqel Lawn Sign</title>
<link href="https://fonts.googleapis.com/css2?family=Nunito:wght@800;900&display=swap" rel="stylesheet">
<style>
  :root {
    --brand-blue: #18519a;
    --canvas-grey: #ececee;
    --canvas-light: #f6f6f7;
    --white: #ffffff;
  }
  html, body {
    margin: 0;
    padding: 0;
    width: 900px;
    height: 1200px;
    overflow: hidden;
    background: var(--canvas-grey);
  }
  .sign {
    position: relative;
    width: 900px;
    height: 1200px;
    overflow: hidden;
    font-family: "Nunito", sans-serif;
  }
  .backdrop {
    position: absolute;
    inset: 0;
    background: linear-gradient(160deg, var(--canvas-light) 0%, var(--canvas-grey) 55%, #e6e6e9 100%);
  }
  .brand-name {
    position: absolute;
    left: 52px;
    top: 128px;
    width: 208px;
    margin: 0;
    text-align: center;
    font-weight: 900;
    font-size: 42px;
    letter-spacing: 2px;
    line-height: 1;
    color: var(--brand-blue);
  }
  .phone-icon {
    position: absolute;
    left: 682px;
    top: 44px;
    width: 66px;
    height: 66px;
  }
  .phone-number {
    position: absolute;
    left: 560px;
    top: 128px;
    width: 310px;
    margin: 0;
    text-align: center;
    font-weight: 900;
    font-size: 30px;
    line-height: 1;
    color: var(--brand-blue);
  }
  .tagline-panel {
    position: absolute;
    left: 0;
    top: 0;
    width: 900px;
    height: 1200px;
  }
  .tagline-panel text {
    font-family: "Nunito", sans-serif;
    font-weight: 900;
    fill: var(--white);
  }
  .corner-phone {
    position: absolute;
    left: 792px;
    top: 976px;
    width: 44px;
    height: 44px;
    opacity: 0.85;
  }
  .footer-band {
    position: absolute;
    left: 0;
    top: 1086px;
    width: 900px;
    height: 114px;
    background: var(--brand-blue);
    color: var(--white);
    font-weight: 800;
  }
  .website {
    position: absolute;
    left: 52px;
    top: 40px;
    margin: 0;
    font-size: 31px;
    letter-spacing: 0.5px;
    line-height: 1;
  }
  .license {
    position: absolute;
    left: 520px;
    top: 12px;
    width: 360px;
    margin: 0;
    text-align: center;
    font-size: 32px;
    line-height: 40px;
  }
</style>
</head>
<body>
<main class="sign">
  <div class="backdrop" role="img" aria-label="Soft light grey background of faint layered geometric tiles"></div>

  <h1 class="brand-name">BRISQEL</h1>

  <svg class="phone-icon" viewBox="0 0 66 66" aria-hidden="true">
    <rect width="66" height="66" rx="6" fill="var(--brand-blue)"/>
    <path d="M22 20c2-2 4-2 5 0l3 5c1 2 0 3-1 4l-2 2c2 4 5 7 9 9l2-2c1-1 2-2 4-1l5 3c2 1 2 3 0 5l-2 2c-3 3-9 1-16-6s-9-13-6-16z" fill="none" stroke="var(--white)" stroke-width="3" stroke-linejoin="round"/>
    <path d="M36 20a10 10 0 0 1 10 10M36 13a17 17 0 0 1 17 17" fill="none" stroke="var(--white)" stroke-width="3" stroke-linecap="round"/>
  </svg>
  <p class="phone-number">(888) BRISQEL-GO</p>

  <svg class="tagline-panel" viewBox="0 0 900 1200" role="img" aria-label="Upgrade your roof without replacing it">
    <polygon points="450,148 816,375 816,770 450,1014 84,770 84,375"
             fill="var(--brand-blue)" stroke="var(--brand-blue)" stroke-width="44" stroke-linejoin="round"/>
    <polygon points="450,150 808,377 808,768 450,1010 92,768 92,377"
             fill="none" stroke="var(--white)" stroke-width="1.2" stroke-linejoin="round"/>
    <text x="169" y="442" font-size="118" textLength="566" lengthAdjust="spacingAndGlyphs">UPGRADE</text>
    <text x="163" y="556" font-size="97" textLength="575" lengthAdjust="spacingAndGlyphs">YOUR ROOF</text>
    <text x="167" y="694" font-size="120" textLength="571" lengthAdjust="spacingAndGlyphs">WITHOUT</text>
    <text x="169" y="792" font-size="87" textLength="568" lengthAdjust="spacingAndGlyphs">REPLACING IT</text>
  </svg>

  <svg class="corner-phone" viewBox="0 0 44 44" aria-hidden="true">
    <path d="M9 10c2-2 3-2 4 0l3 4c1 2 0 3-1 4l-1 1c2 3 4 5 7 7l1-1c1-1 2-2 4-1l4 3c2 1 2 2 0 4l-2 2c-3 2-8 0-13-5s-8-11-6-14z" fill="none" stroke="var(--white)" stroke-width="2.6" stroke-linejoin="round"/>
    <path d="M24 8a9 9 0 0 1 9 9M24 2a15 15 0 0 1 15 15" fill="none" stroke="var(--white)" stroke-width="2.6" stroke-linecap="round"/>
  </svg>

  <footer class="footer-band">
    <p class="website">www.trybrisqel.com</p>
    <p class="license">TWQB License Number<br>4480512</p>
  </footer>
</main>
</body>
</html>
```